Executive Business Card for Healthcare Company [Need Today]

I need a business card design for a healthcare company. The only branding the company has thus far is a logo. The cards will be utilized by company executives. The design I envision will be vibrant and appealing but with a corporate feel. They shouldn't be too casual or playful. I would like to complete this project TODAY if possible.

Target Market(s)

Healthcare vendors, other executives in healthcare and pharmaceuticals

Industry/Entity Type

Pharmaceutical

Contact Information for Business Card

See attachment

Font styles to use
Serif
Sans Serif

Colors

Designer to choose colors to be used in the design.

```html
<!DOCTYPE html>
<html lang="en">
<head>
<meta charset="utf-8">
<title>Corvane Therapeutics – Business Card</title>
<link rel="stylesheet" href="https://fonts.googleapis.com/css2?family=Open+Sans:wght@300;400;600&family=Oswald:wght@500&display=swap">
<style>
  :root {
    --teal: #35bec6;
    --teal-deep: #2fb3bb;
    --green: #3aaa6e;
    --green-band: #45b27a;
    --ink: #333333;
    --paper: #fbfbfa;
    --backdrop: #e9ecec;
    --white: #ffffff;
  }
  * { box-sizing: border-box; margin: 0; padding: 0; }
  html, body { width: 1200px; height: 1000px; overflow: hidden; }
  body {
    background: var(--backdrop);
    font-family: "Open Sans", Arial, sans-serif;
    position: relative;
  }
  .card {
    position: absolute;
    width: 560px;
    height: 320px;
    border-radius: 18px;
    overflow: hidden;
    box-shadow: 0 10px 28px rgba(0,0,0,0.14);
  }
  /* Front */
  .card-front {
    left: 90px; top: 90px;
    background: var(--teal);
  }
  .card-front .pattern-area {
    position: absolute; inset: 0;
    background: var(--teal);
  }
  .front-brand {
    position: absolute;
    left: 0; right: 0; top: 0; bottom: 0;
    display: flex; align-items: center; justify-content: center;
    gap: 22px;
  }
  .front-brand .brand-dot {
    width: 104px; height: 104px;
    border: 2px solid var(--white);
    border-radius: 50%;
  }
  .front-brand .brand-name {
    color: var(--white);
    font-weight: 300;
    font-size: 34px;
    line-height: 1.15;
    letter-spacing: 0.5px;
  }
  /* Back */
  .card-back {
    left: 550px; top: 590px;
    background: var(--paper);
  }
  .back-brand {
    position: absolute;
    left: 170px; top: 36px;
    display: flex; align-items: center; gap: 16px;
  }
  .back-brand .brand-dot {
    width: 70px; height: 70px;
    border: 1.5px solid var(--green);
    border-radius: 50%;
  }
  .back-brand .brand-name {
    color: var(--teal);
    font-weight: 300;
    font-size: 24px;
    line-height: 1.15;
  }
  .company-address {
    position: absolute;
    right: 30px; top: 150px;
    text-align: right;
    font-size: 12.5px;
    line-height: 1.4;
    color: var(--ink);
  }
  .rule {
    position: absolute;
    left: 26px; right: 26px; top: 212px;
    height: 1px;
    background: var(--green);
  }
  .person {
    position: absolute;
    left: 26px; top: 170px;
  }
  .person-name {
    font-family: "Oswald", "Arial Narrow", sans-serif;
    font-weight: 500;
    font-size: 19px;
    color: var(--green);
    letter-spacing: 0.5px;
    line-height: 1.1;
  }
  .person-title {
    font-size: 13px;
    color: var(--ink);
    line-height: 1.3;
  }
  .contact-list {
    position: absolute;
    left: 26px; top: 222px;
    list-style: none;
    font-size: 12.5px;
    color: var(--ink);
    line-height: 1.45;
  }
  .contact-list li { display: flex; align-items: center; gap: 7px; }
  .contact-list li.no-icon { padding-left: 17px; }
  .contact-list svg { width: 10px; height: 10px; flex: none; }
  .bands {
    position: absolute; left: 0; bottom: 0;
    width: 560px; height: 90px;
  }
</style>
</head>
<body>

  <section class="card card-front" aria-label="Card front">
    <div class="pattern-area" role="img" aria-label="Faint repeating brand-mark pattern over teal"></div>
    <div class="front-brand">
      <span class="brand-dot"></span>
      <span class="brand-name">Corvane<br>Therapeutics</span>
    </div>
  </section>

  <section class="card card-back" aria-label="Card back">
    <div class="back-brand">
      <span class="brand-dot"></span>
      <span class="brand-name">Corvane<br>Therapeutics</span>
    </div>

    <address class="company-address" style="font-style:normal">
      Corvane Therapeutics, LLC<br>
      118 Linden Court<br>
      Fairview, GA 30599
    </address>

    <div class="person">
      <p class="person-name">DANIEL MERCER</p>
      <p class="person-title">Senior Director of Marketing</p>
    </div>

    <div class="rule"></div>

    <ul class="contact-list">
      <li>
        <svg viewBox="0 0 10 10" aria-hidden="true"><path d="M2 1 L4 1 L4.6 3 L3.5 4 Q4.5 6 6 6.5 L7 5.4 L9 6 L9 8 Q9 9 8 9 Q1 8.5 1 2 Q1 1 2 1Z" fill="var(--green)"/></svg>
        555-210-4837 (Office)
      </li>
      <li class="no-icon">555-318-6205 (Cell)</li>
      <li>
        <svg viewBox="0 0 10 10" aria-hidden="true"><rect x="0.5" y="1.5" width="9" height="7" rx="1" fill="var(--green)"/><path d="M1 2.5 L5 5.5 L9 2.5" stroke="#fff" stroke-width="0.9" fill="none"/></svg>
        dmercer@corvanerx.com
      </li>
    </ul>

    <svg class="bands" viewBox="0 0 560 90" aria-hidden="true">
      <path d="M0 72 L380 30 Q400 28 408 14 Q414 4 430 4 L560 4 L560 90 L0 90Z" fill="var(--teal)"/>
      <path d="M0 80 L385 38 Q404 36 412 22 Q418 12 434 12 L560 12 L560 90 L0 90Z" fill="var(--green-band)"/>
    </svg>
  </section>

</body>
</html>
```